Business cards for KORU Real Estate Holdings LLC

We need a cool, original business card design for a company based in the Washington DC metropolitan area. We are a new energetic and passionate Real Estate Investing Company that invests in all types of real estate; commercial, residential, industrial etc.

Our company color is Red since it reflects action, energy and speed; it is assertive confident, energizing, exciting, powerful, passionate and determined. So we would like business card communicate those qualities to the audience.

Our audiences are investors that want to invest with us, real estate sellers, buyers, and tenants who lease from us.

Our logo is attached

```html
<!DOCTYPE html>
<html lang="en">
<head>
<meta charset="utf-8">
<title>KORU Real Estate Holdings LLC — Business Card</title>
<link rel="stylesheet" href="https://fonts.googleapis.com/css2?family=Open+Sans:wght@400;600;700;800&display=swap">
<style>
  :root {
    --backdrop: #e7e4df;
    --card-light: #dcd9d3;
    --card-light-edge: #c9c6bf;
    --card-dark: #1c1c1d;
    --card-dark-soft: #2e2e30;
    --silver: #d9d9d9;
    --accent-red: #d8232a;
    --ink: #3a3a3c;
    --ink-soft: #5a5a5c;
    --paper: #ffffff;
  }
  * { box-sizing: border-box; margin: 0; padding: 0; }
  html, body {
    width: 1200px;
    height: 798px;
    overflow: hidden;
    background: var(--backdrop);
    font-family: "Open Sans", Arial, sans-serif;
  }
  .business-card {
    position: absolute;
    left: 160px;
    top: 144px;
    width: 880px;
    height: 510px;
    border-radius: 22px;
    overflow: hidden;
    background: linear-gradient(160deg, #e6e3de 0%, var(--card-light) 55%, var(--card-light-edge) 100%);
    box-shadow: 0 18px 40px rgba(0,0,0,0.18);
  }
  .card-swoosh {
    position: absolute;
    inset: 0;
    width: 100%;
    height: 100%;
  }
  .brand {
    position: absolute;
    left: 78px;
    top: 118px;
    display: flex;
    align-items: center;
    gap: 22px;
  }
  .brand-mark {
    width: 44px;
    height: 44px;
    background: var(--accent-red);
  }
  .brand-name {
    font-weight: 700;
    font-size: 92px;
    line-height: 1;
    letter-spacing: 2px;
    color: var(--ink);
  }
  .person {
    position: absolute;
    left: 58px;
    top: 272px;
    color: var(--ink);
  }
  .person-name {
    font-size: 30px;
    line-height: 1.1;
  }
  .person-name .first { font-weight: 700; }
  .person-name .last { font-weight: 400; }
  .person-title {
    margin-top: 6px;
    font-size: 17px;
    color: var(--ink-soft);
  }
  .contact {
    position: absolute;
    left: 636px;
    top: 330px;
    color: var(--paper);
    font-size: 17px;
    line-height: 27px;
    list-style: none;
  }
  .contact li {
    display: flex;
    align-items: center;
    gap: 10px;
  }
  .contact-icon {
    width: 16px;
    height: 16px;
    flex: none;
  }
</style>
</head>
<body>
  <article class="business-card">
    <svg class="card-swoosh" viewBox="0 0 880 510" preserveAspectRatio="none" aria-hidden="true">
      <defs>
        <linearGradient id="darkPanel" x1="0" y1="0" x2="1" y2="1">
          <stop offset="0" stop-color="#2e2e30"/>
          <stop offset="1" stop-color="#151516"/>
        </linearGradient>
      </defs>
      <path d="M0 462 C 260 424, 600 318, 880 70 L880 510 L0 510 Z" fill="var(--silver)"/>
      <path d="M0 476 C 270 442, 610 338, 880 92 L880 510 L0 510 Z" fill="url(#darkPanel)"/>
      <path d="M170 440 C 420 392, 660 296, 862 70 C 670 308, 430 404, 170 440 Z" fill="var(--accent-red)" stroke="var(--accent-red)" stroke-width="3" stroke-linejoin="round"/>
    </svg>

    <div class="brand">
      <span class="brand-mark"></span>
      <span class="brand-name">KORU</span>
    </div>

    <div class="person">
      <p class="person-name"><span class="first">Daniel</span> <span class="last">Reyes</span></p>
      <p class="person-title">Owner / C.E.O.</p>
    </div>

    <ul class="contact">
      <li>1250 Harbor Lane</li>
      <li>Suite # 210</li>
      <li>
        <svg class="contact-icon" viewBox="0 0 16 16" aria-hidden="true"><circle cx="8" cy="8" r="8" fill="#fff"/><path d="M5 4 L7 4 L7.5 6 L6.5 7 C7 8.5 8 9.5 9 10 L10 9 L12 9.5 L12 11.5 C8 12 4.5 8.5 5 4 Z" fill="#1c1c1d"/></svg>
        202-555-0147
      </li>
      <li>
        <svg class="contact-icon" viewBox="0 0 16 16" aria-hidden="true"><circle cx="8" cy="8" r="8" fill="#fff"/><rect x="5.5" y="3.5" width="5" height="9" rx="1" fill="#1c1c1d"/><rect x="6.5" y="5" width="3" height="5" fill="#fff"/></svg>
        202-555-0148
      </li>
      <li>
        <svg class="contact-icon" viewBox="0 0 16 16" aria-hidden="true"><circle cx="8" cy="8" r="8" fill="#fff"/><rect x="4" y="7" width="8" height="5" rx="1" fill="#1c1c1d"/><rect x="5.5" y="4" width="5" height="3.5" fill="#1c1c1d"/></svg>
        202-555-0149
      </li>
      <li>
        <svg class="contact-icon" viewBox="0 0 16 16" aria-hidden="true"><rect x="1" y="3.5" width="14" height="9" rx="1" fill="#fff"/><path d="M1.5 4 L8 9 L14.5 4" fill="none" stroke="#1c1c1d" stroke-width="1.2"/></svg>
        info@koruholdings.com
      </li>
    </ul>
  </article>
</body>
</html>
```